Counseling Practice Business Card

I need a professional looking business card incorporating my new logo that was just completed. Card needs to incorporate my name and title, description of my specialty, my address, my phone number, my fax number, my email and my website URL. I need to be able to choose design on/with different paper colors and textures.
I do not have a lot of business card ideas so I am open to anything but I want bold,sharp, clear card without additional designs other than my logo (see attached file info). I am open to different color backgrounds or paper colors including black. I do not like traditional brackets around area codes in phone number or dashes between numbers in phone number. Am open to other ways of presenting including periods between numbers as appropriate. I do not know enough to know what I like yet but I want card to coordinate and work together with my logo. My practice emphasizes natural mental health interventions so any use of color (with background paper color or the blue and green in my logo) that elicits nature is nice. In addition to black, any natural brown or wood looking background might be desirable also. Most of the offerings so far look very similar and boring.

Target Market(s)

Potential therapy clients and other professionals

Contact Information for Business Card

Card information:
Gerald M. Whitcombe, Ph.D.
Licensed Clinical Psychologist
Integrative Health Coach
4812 Marlowe Ridge Blvd SE
Suite 310
Duluth, GA 30096
(770) 415-2983 phone
(770) 581-4096 fax
drgeraldwhitcombe@quillmarsh.net
brightfernwellness.net

Font styles to use
Serif
Sans Serif
Other font styles liked:
• anything that you think looks crisp, clear and easily readable

Requirements
Must have
• Any color used should coordinate with my logo design (see attached files).
• Card should be printed horizontally so top and bottom are longest sides of rectangle.
• Background color or paper color should complement and highlight logo. Do not like a white background. black, grey, brown or any color my logo would blend well with.
Nice to have
• I would like designer to utilize color to highlight letters/name or phone-fax-web symbols.
• Bottom edge of card could be highlighted if appropriate to an idea.
Should not have
• I would NOT want the card to have a pure white background at all.
• No clear cards.
• Cards should be oriented with long sides on bottom and top, NOT sides. DO NOT LIKE THIS THIN TALL ORIENTATION.

```html
<!DOCTYPE html>
<html lang="en">
<head>
<meta charset="utf-8">
<title>Brightfern Wellness – Business Card</title>
<link rel="stylesheet" href="https://fonts.googleapis.com/css2?family=Roboto+Condensed:wght@700&family=Roboto:wght@400;500&display=swap">
<style>
  :root {
    --backdrop: #4a4a4c;
    --card-black: #1d1e21;
    --emboss: #2c2d31;
    --brand-blue: #3a8fd6;
    --blue-light: #4aa3e6;
    --blue-deep: #2a76c0;
    --brand-green: #1f8a47;
    --white: #ffffff;
  }
  * { margin: 0; padding: 0; box-sizing: border-box; }
  html, body {
    width: 1200px;
    height: 752px;
    overflow: hidden;
    background: var(--backdrop);
  }
  .canvas {
    position: relative;
    width: 1200px;
    height: 752px;
    display: flex;
    align-items: center;
    justify-content: center;
    gap: 60px;
  }
  .card {
    position: relative;
    width: 500px;
    height: 286px;
    border-radius: 4px;
    overflow: hidden;
    background: var(--card-black);
  }

  /* Front */
  .card-front {
    display: flex;
    align-items: center;
    justify-content: center;
  }
  .front-wordmark {
    display: flex;
    align-items: center;
    gap: 14px;
  }
  .front-mark {
    width: 22px;
    height: 22px;
    border-radius: 50%;
    background: var(--emboss);
  }
  .front-name {
    font-family: "Roboto Condensed", sans-serif;
    font-weight: 700;
    font-size: 40px;
    letter-spacing: 1px;
    color: var(--emboss);
  }

  /* Back */
  .back-shapes {
    position: absolute;
    inset: 0;
  }
  .holder {
    position: absolute;
    left: 26px;
    top: 20px;
    font-family: "Roboto Condensed", sans-serif;
  }
  .holder-name {
    font-weight: 700;
    font-size: 15px;
    letter-spacing: 0.5px;
    text-transform: uppercase;
    color: var(--brand-blue);
  }
  .holder-title {
    font-family: "Roboto", sans-serif;
    font-size: 10px;
    line-height: 1.35;
    color: var(--brand-green);
  }
  .back-wordmark {
    position: absolute;
    left: 26px;
    top: 80px;
    display: flex;
    align-items: center;
    gap: 10px;
  }
  .back-mark {
    width: 16px;
    height: 16px;
    border-radius: 50%;
    background: var(--brand-blue);
  }
  .back-name {
    font-family: "Roboto Condensed", sans-serif;
    font-weight: 700;
    font-size: 30px;
    color: var(--brand-blue);
  }
  .contact {
    position: absolute;
    right: 22px;
    bottom: 22px;
    text-align: right;
    font-family: "Roboto", sans-serif;
    font-size: 11.5px;
    line-height: 1.45;
    color: var(--white);
  }
  .address { margin-bottom: 6px; }
  .contact-line {
    display: flex;
    justify-content: flex-end;
    align-items: center;
    gap: 6px;
  }
  .contact-icon {
    width: 11px;
    height: 11px;
    flex: none;
  }
</style>
</head>
<body>
<main class="canvas">

  <section class="card card-front" aria-label="Card front">
    <div class="front-wordmark">
      <span class="front-mark"></span>
      <span class="front-name">Brightfern Wellness</span>
    </div>
  </section>

  <section class="card card-back" aria-label="Card back">
    <svg class="back-shapes" viewBox="0 0 500 286" preserveAspectRatio="none" aria-hidden="true">
      <defs>
        <linearGradient id="blueField" x1="0" y1="0" x2="1" y2="1">
          <stop offset="0" stop-color="var(--blue-light)"/>
          <stop offset="1" stop-color="var(--blue-deep)"/>
        </linearGradient>
      </defs>
      <rect width="500" height="286" fill="url(#blueField)"/>
      <path d="M0 0 H440 C380 110 230 172 0 178 Z" fill="var(--brand-green)"/>
      <path d="M0 0 H410 C350 100 215 160 0 166 Z" fill="var(--card-black)"/>
    </svg>

    <div class="holder">
      <p class="holder-name">Gerald M. Whitcombe, Ph.D.</p>
      <p class="holder-title">Licensed Clinical Psychologist</p>
      <p class="holder-title">Integrative Health Coach</p>
    </div>

    <div class="back-wordmark">
      <span class="back-mark"></span>
      <span class="back-name">Brightfern Wellness</span>
    </div>

    <div class="contact">
      <p class="address">4812 Marlowe Ridge Blvd SE<br>Suite 310<br>Duluth, GA 30096</p>
      <p class="contact-line">(770) 415-2983
        <svg class="contact-icon" viewBox="0 0 12 12" aria-label="Phone"><path d="M2.5 1 L4.5 1 L5.3 3.4 L4 4.4 C4.6 5.8 6.2 7.4 7.6 8 L8.6 6.7 L11 7.5 L11 9.5 C11 10.3 10.3 11 9.5 11 C5 11 1 7 1 2.5 C1 1.7 1.7 1 2.5 1 Z" fill="var(--white)"/></svg>
      </p>
      <p class="contact-line">(770) 581-4096
        <svg class="contact-icon" viewBox="0 0 12 12" aria-label="Fax"><rect x="3" y="1" width="6" height="3" fill="var(--white)"/><rect x="1" y="4.5" width="10" height="5" rx="1" fill="var(--white)"/><rect x="3" y="8" width="6" height="3" fill="var(--white)"/></svg>
      </p>
      <p class="contact-line">drgeraldwhitcombe@quillmarsh.net
        <svg class="contact-icon" viewBox="0 0 12 12" aria-label="Email"><rect x="0.5" y="2.5" width="11" height="7.5" rx="1" fill="var(--white)"/><path d="M1 3 L6 7 L11 3" stroke="var(--blue-deep)" stroke-width="1" fill="none"/></svg>
      </p>
      <p class="contact-line">brightfernwellness.net
        <svg class="contact-icon" viewBox="0 0 12 12" aria-label="Website"><circle cx="6" cy="6" r="5.2" fill="var(--white)"/><ellipse cx="6" cy="6" rx="2.2" ry="5.2" stroke="var(--blue-deep)" stroke-width="0.8" fill="none"/><path d="M1 6 H11" stroke="var(--blue-deep)" stroke-width="0.8"/></svg>
      </p>
    </div>
  </section>

</main>
</body>
</html>
```